Web Design Project

Looking for an eye catching banner page to be used on the website and LinkedIn. We are an Executive Recruiting and HR Consulting service firm with a modern edge. We want to demonstrate through our brand that we are using the latest recruiting trends to find talent and that we are easy to work with- innovative and simple.We typically recruit for Engineers, IT professionals, Accounting and Operation Managers. Our website is www.bluvantatalent.com and it needs a fresh clean look. We love our logo but might want to use the "8" to show the 2 sides of our business or maybe to use the infinity concept or continuous improvement. We like the Green and white colors with accents in gray.

Target Market(s)

Small to mid-sized Business Managers seeking innovation

Industry/Entity Type

Business

Requirements
Must have
• Use of the 8
Long picture on top to be used on LinkedIn and the website top
Clean Simple look- modern font like century gothic
Nice to have
• Smiling face(s)
Layered image of 8 or of photo stock faces
Maybe a modern office so they feel that they walked in to meet us (fyi our office has white chandeliers and green walls that match our logo)
Should not have
• Busy or cluttered feel

```html
<!DOCTYPE html>
<html lang="en">
<head>
<meta charset="utf-8">
<title>Bluvanta – Where Strategy Meets Recruiting</title>
<link rel="stylesheet" href="https://fonts.googleapis.com/css2?family=Questrial&family=Arimo:wght@400;700&display=swap">
<style>
:root{
  --green:#9cc43a;
  --green-light:#b9d94f;
  --green-dark:#7ea32a;
  --footer:#8ea543;
  --footer-dark:#7b9236;
  --gray:#8f969b;
  --gray-dark:#6b7176;
  --band:#ececec;
  --text:#333;
  --muted:#555;
  --dark:#3d4145;
  --white:#fff;
}
*{box-sizing:border-box;margin:0;padding:0}
html,body{width:1000px;height:1200px;overflow:hidden;background:var(--white)}
body{font-family:"Arimo",Arial,sans-serif;color:var(--text);font-size:10px;position:relative}
.abs{position:absolute}
.topline{left:0;top:0;width:1000px;height:6px;background:var(--green)}
.brand{left:186px;top:42px}
.brand-name{font-family:"Questrial",sans-serif;font-size:44px;color:var(--green);letter-spacing:1px;line-height:50px;white-space:nowrap}
.brand-tag{font-family:"Questrial",sans-serif;font-size:8.5px;letter-spacing:2.2px;color:var(--dark);margin-top:4px;white-space:nowrap}
.utility{right:188px;top:22px;font-size:9px;font-weight:700;display:flex;gap:14px;white-space:nowrap}
.utility span{display:flex;align-items:center;gap:4px}
.btn{background:linear-gradient(var(--green-light),var(--green));color:var(--white);font-size:12px;display:flex;align-items:center;justify-content:center;border:1px solid var(--green-dark);border-radius:2px;white-space:nowrap}
.btn-candidate{left:619px;top:56px;width:92px;height:27px}
.btn-clients{left:718px;top:56px;width:94px;height:27px}
.search{left:686px;top:92px;width:126px;height:20px;border:1px solid var(--green);font-style:italic;color:var(--green-dark);font-size:10px;padding:4px 8px}
.search svg{position:absolute;right:5px;top:4px}
.nav{left:186px;top:119px;width:626px;height:32px;background:linear-gradient(#a1a7ab,var(--gray));border:1px solid #7d8388;display:flex;align-items:center;padding-left:45px;gap:14px;color:var(--white);font-size:9.5px;white-space:nowrap;overflow:hidden}
.nav span{flex:none}
.nav .active{border-bottom:3px solid var(--white);padding:8px 0 5px}
.hero{left:186px;top:160px;width:626px;height:216px;background:linear-gradient(90deg,#e8efe0 0%,#d8e3c4 35%,#cdd4d8 60%,#b9c1c6 100%)}
.hero-caption{left:186px;top:340px;width:626px;height:36px;background:rgba(140,186,40,.88);color:var(--white);font-size:13px;line-height:15px;padding:3px 14px}
.arrow{width:20px;height:20px}
.intro-mark{left:202px;top:389px}
.intro-line{left:186px;top:417px;width:626px;height:1px;background:var(--green)}
.intro-title{right:188px;top:386px;font-family:"Questrial",sans-serif;font-size:22px;color:var(--dark);white-space:nowrap}
.intro-text{left:186px;top:455px;width:620px;font-size:9px;line-height:11px;color:var(--text)}
.intro-text p{margin-bottom:9px}
.btn-small{font-size:8px;font-weight:700;height:15px}
.learn{left:745px;top:515px;width:58px}
.band{left:0;top:542px;width:1000px;height:125px;background:var(--band);border-top:1px solid #dcdcdc;border-bottom:1px solid #dcdcdc}
.service{width:170px;text-align:center;font-family:"Questrial",sans-serif;font-size:12.5px;color:var(--dark);white-space:nowrap}
.service svg{display:block;margin:0 auto 6px}
.numbers{left:186px;top:684px;width:414px;height:200px;border:1px solid #d6d6d6;background:#eeeee6}
.numbers-head{height:32px;background:linear-gradient(var(--green-light),var(--green));display:flex;align-items:center;gap:10px;padding-left:8px;font-family:"Questrial",sans-serif;color:var(--white);font-size:17px;white-space:nowrap}
.numbers-list{list-style:none;padding:10px 30px 0 10px;font-size:9px;line-height:13px}
.numbers-list li{display:flex;gap:8px;margin-bottom:12px}
.numbers-list svg{flex:none;margin-top:1px}
.scroll{right:10px;top:42px;width:5px;height:112px;background:#ddd;border:1px solid #ccc}
.scroll::after{content:"";position:absolute;left:0;top:0;width:3px;height:28px;background:#fff}
.testimonials{left:619px;top:684px;width:193px;height:200px;border:1px solid #ddd;background:var(--white);padding:10px 16px}
.testimonials h2{font-family:"Questrial",sans-serif;font-weight:400;font-size:17px;color:var(--dark);margin-bottom:16px}
.testimonials p{font-size:9px;line-height:13px;text-align:justify}
.testimonials cite{display:block;text-align:right;font-style:italic;font-weight:700;font-size:9px;margin-top:2px;white-space:nowrap}
.more-test{left:100px;top:173px;width:86px}
.footer{left:0;top:940px;width:1000px;height:230px;background:radial-gradient(ellipse at 50% 90%,#b0c668 0%,var(--footer) 55%,var(--footer-dark) 100%)}
.social-tab{left:412px;top:912px;width:176px;height:30px}
.social{left:428px;top:920px;display:flex;gap:4px}
.social span{width:18px;height:18px;border-radius:2px;background:var(--white);opacity:.92}
.fcol{color:var(--white);font-size:9px}
.fcol h3{font-family:"Questrial",sans-serif;font-weight:400;font-size:13px;padding-bottom:6px;border-bottom:1px solid rgba(255,255,255,.5);margin-bottom:8px;width:100px;white-space:nowrap}
.fcol li{list-style:none;line-height:16.5px;white-space:nowrap}
.about{left:191px;top:972px}
.contact{left:317px;top:972px}
.contact .row{display:flex;gap:10px;align-items:center;margin-bottom:10px;white-space:nowrap}
.contact .big{font-family:"Questrial",sans-serif;font-size:14px}
.badge{left:189px;top:1104px;width:104px;height:50px;background:var(--white);border-radius:6px;border:2px solid #e0e6cc}
.jobs{left:469px;top:974px;width:157px;height:180px;background:var(--white);border:1px solid #ddd}
.jobs-head{height:26px;background:linear-gradient(var(--green-light),var(--green));color:var(--white);font-family:"Questrial",sans-serif;font-size:13px;text-align:center;line-height:26px}
.jobs ul{list-style:none;padding:10px 8px;font-size:8.5px;color:var(--muted);line-height:11px}
.jobs li{margin-bottom:8px}
.more-vac{left:37px;top:154px;width:86px}
.social-box{left:644px;top:974px;width:158px;height:180px;background:var(--white);border:1px solid #ddd;padding:8px}
.sb-head{display:flex;align-items:center;gap:6px;font-size:10px;font-weight:700;color:#3b5a8f}
.sb-like{border:1px solid #bbb;font-size:7.5px;padding:1px 4px;color:#333;font-weight:400}
.sb-count{font-size:7px;color:#444;margin:12px 0 4px;white-space:nowrap}
.faces{display:grid;grid-template-columns:repeat(4,32px);gap:4px}
.faces span{height:30px;background:linear-gradient(#c9c4bc,#8f8a84)}
.sb-foot{position:absolute;left:0;bottom:0;width:100%;border-top:1px solid #ddd;font-size:7px;color:#555;padding:4px 6px}
.copy{left:0;top:1170px;width:1000px;height:30px;background:linear-gradient(#5a5f63,#3d4145);color:#e6e6e6;font-size:8px;text-align:center;line-height:30px;white-space:nowrap}
</style>
</head>
<body>
<div class="abs topline"></div>

<header>
  <div class="abs brand">
    <div class="brand-name">BLUVANTA</div>
    <div class="brand-tag">WHERE STRATEGY MEETS RECRUITING</div>
  </div>
  <div class="abs utility">
    <span><svg width="11" height="10" viewBox="0 0 11 10"><path d="M1 5 5.5 1 10 5M2.5 4v5h6V4" fill="none" stroke="#333" stroke-width="1.6"/></svg>Home</span>
    <span><svg width="11" height="9" viewBox="0 0 11 9"><rect x=".5" y=".5" width="10" height="8" fill="#333"/><path d="M1 1l4.5 4L10 1" stroke="#fff" fill="none"/></svg>Contact</span>
  </div>
  <div class="abs btn btn-candidate">Candidate</div>
  <div class="abs btn btn-clients">Clients</div>
  <div class="abs search">Search
    <svg width="11" height="11" viewBox="0 0 11 11"><circle cx="4.5" cy="4.5" r="3.3" fill="none" stroke="#9cc43a" stroke-width="1.5"/><path d="M7 7l3 3" stroke="#9cc43a" stroke-width="1.8"/></svg>
  </div>
  <nav class="abs nav">
    <span class="active">Recruiting Services</span><span>HR consulting Services</span><span>Testimonials</span><span>Job Openings</span><span>Job Search Assistance</span><span>Job Application</span><span>Blog</span>
  </nav>
</header>

<section>
  <div class="abs hero" role="img" aria-label="Photo of five smiling recruiting professionals in a bright modern office with green accents"></div>
  <div class="abs hero-caption">Bluvanta demonstrated extraordinary insight in understanding both the client recruiting needs and the candidates' objectives"</div>
  <svg class="abs arrow" style="left:180px;top:256px" viewBox="0 0 20 20"><circle cx="10" cy="10" r="8.5" fill="#fff" stroke="#9cc43a" stroke-width="2"/><path d="M11.5 6 7.5 10l4 4" fill="none" stroke="#9cc43a" stroke-width="2"/></svg>
  <svg class="abs arrow" style="left:797px;top:256px" viewBox="0 0 20 20"><circle cx="10" cy="10" r="8.5" fill="#fff" stroke="#9cc43a" stroke-width="2"/><path d="M8.5 6l4 4-4 4" fill="none" stroke="#9cc43a" stroke-width="2"/></svg>
</section>

<section>
  <div class="abs intro-line"></div>
  <svg class="abs intro-mark" width="54" height="54" viewBox="0 0 54 54"><circle cx="27" cy="27" r="25" fill="#fff" stroke="#9cc43a" stroke-width="3"/></svg>
  <h1 class="abs intro-title" style="font-weight:400">Where strategy meets recruiting</h1>
  <div class="abs intro-text">
    <p>The modern and successful recruiting leader begins with a strategic foundation, leverages connectivity through social media, stakeholder relationships and builds pipelines of competencies, quickly and flexibly to solve pressing employment challenges.</p>
    <p>Bluvanta combines strategy and action to find top talent in the areas of Engineering, IT, Operations, and Accounting and Administration. Look to Bluvanta to explore new pathways to strategic relevancy.&nbsp; From strategy to execution, we are the team you need… NOW!</p>
    <p>How can we be your strategic partner to success?</p>
  </div>
  <div class="abs btn btn-small learn">Learn more</div>
</section>

<section class="abs band">
  <div class="abs service" style="left:201px;top:14px">
    <svg width="76" height="76" viewBox="0 0 76 76"><circle cx="38" cy="38" r="36" fill="#8d9397" stroke="#dedede" stroke-width="3"/><circle cx="30" cy="30" r="7" fill="#3d4145"/><circle cx="46" cy="30" r="7" fill="#3d4145"/><path d="M18 52q12-16 24 0zM34 52q12-16 24 0z" fill="#3d4145"/></svg>
    Expert Recruiting
  </div>
  <div class="abs service" style="left:413px;top:14px">
    <svg width="76" height="76" viewBox="0 0 76 76"><circle cx="38" cy="38" r="36" fill="#8d9397" stroke="#dedede" stroke-width="3"/><rect x="20" y="30" width="16" height="16" fill="#fff"/><circle cx="36" cy="38" r="4" fill="#fff"/><rect x="40" y="30" width="16" height="16" fill="#3d4145"/><circle cx="48" cy="30" r="4" fill="#3d4145"/></svg>
    Recruiting Strategy
  </div>
  <div class="abs service" style="left:629px;top:14px">
    <svg width="76" height="76" viewBox="0 0 76 76"><circle cx="38" cy="38" r="36" fill="#8cc12c" stroke="#dedede" stroke-width="3"/><circle cx="38" cy="29" r="8" fill="#3d4145"/><path d="M22 56q16-22 32 0z" fill="#3d4145"/></svg>
    Human Resource Consulting
  </div>
</section>

<section class="abs numbers">
  <div class="numbers-head">
    <svg width="24" height="24" viewBox="0 0 24 24"><circle cx="12" cy="12" r="10.5" fill="#fff"/></svg>
    Here at Bluvanta, we love our numbers!
  </div>
  <ul class="numbers-list">
    <li><svg width="10" height="10" viewBox="0 0 10 10"><circle cx="5" cy="5" r="5" fill="#9cc43a"/><path d="M4 3l2 2-2 2" stroke="#fff" fill="none" stroke-width="1.3"/></svg><span>8 is known as the beginning and long symbolized for good luck, to us it means that and more!</span></li>
    <li><svg width="10" height="10" viewBox="0 0 10 10"><circle cx="5" cy="5" r="5" fill="#9cc43a"/><path d="M4 3l2 2-2 2" stroke="#fff" fill="none" stroke-width="1.3"/></svg><span>76% of all employees are passively searching for a new position, we must find ways to keep your talent engaged as well as identiy the right new talent for your organization</span></li>
    <li><svg width="10" height="10" viewBox="0 0 10 10"><circle cx="5" cy="5" r="5" fill="#9cc43a"/><path d="M4 3l2 2-2 2" stroke="#fff" fill="none" stroke-width="1.3"/></svg><span>52% of companies are expecting to grow in the next 6 months</span></li>
    <li><svg width="10" height="10" viewBox="0 0 10 10"><circle cx="5" cy="5" r="5" fill="#9cc43a"/><path d="M4 3l2 2-2 2" stroke="#fff" fill="none" stroke-width="1.3"/></svg><span>$8,947 is the national average cost per hire—up approximately 57% from $5,708 in 2009, we can show you how to reduce the cost and increase quality</span></li>
  </ul>
  <div class="abs scroll"></div>
</section>

<section class="abs testimonials">
  <h2>Testimonials</h2>
  <p>Bluvanta has been very attentive to the needs of our Corporation. From providing administrative to technical candidates, they operate in a professional manor and will go above and beyond to achieve exceptional results.</p>
  <cite>Orbital Contract Company</cite>
  <div class="abs btn btn-small more-test">More Testimonials</div>
</section>

<footer>
  <div class="abs footer"></div>
  <svg class="abs social-tab" viewBox="0 0 176 30"><path d="M0 30 12 2Q13 0 16 0H160q3 0 4 2L176 30Z" fill="#8ea543"/></svg>
  <div class="abs social" aria-label="Social links">
    <span></span><span></span><span></span><span></span><span></span><span></span>
  </div>

  <div class="abs fcol about">
    <h3>About Bluvanta</h3>
    <ul><li>About Us</li><li>What we do</li><li>How we do</li><li>Testimonials</li><li>Our awards</li><li>Our Partners</li></ul>
  </div>
  <div class="abs badge" role="img" aria-label="Certification badge"></div>

  <div class="abs fcol contact">
    <h3>Contact Us</h3>
    <ul style="margin-bottom:8px"><li>Contact Bluvanta</li><li>Help &amp; Links</li></ul>
    <div class="row"><svg width="12" height="16" viewBox="0 0 12 16"><path d="M6 15C2 9 1 7 1 5.5a5 5 0 0 1 10 0C11 7 10 9 6 15z" fill="#fff"/><circle cx="6" cy="5.5" r="2" fill="#8ea543"/></svg><span>2210 Lakeview Drive<br>Houston, TX, 77001</span></div>
    <div class="row"><svg width="14" height="11" viewBox="0 0 14 11"><rect x=".5" y=".5" width="13" height="10" fill="#fff"/><path d="M1 1l6 5 6-5" stroke="#8ea543" fill="none"/></svg><span>info@bluvantatalent.com</span></div>
    <div class="row"><svg width="14" height="14" viewBox="0 0 14 14"><path d="M3 1l3 3-2 2q2 3 4 4l2-2 3 3-2 2Q5 13 1 3z" fill="#fff"/></svg><span class="big">281.555.0142</span></div>
    <div class="row"><svg width="14" height="13" viewBox="0 0 14 13"><rect x="3" y="0" width="8" height="4" fill="#fff"/><rect x="0" y="4" width="14" height="6" fill="#fff"/><rect x="3" y="9" width="8" height="4" fill="#fff" stroke="#8ea543"/></svg><span class="big">713.555.0187</span></div>
  </div>

  <div class="abs jobs">
    <div class="jobs-head">Job Openings</div>
    <ul>
      <li>- Houstan is hiring</li>
      <li>- Northwell Consulting is looking for a decent Art director</li>
      <li>- Corvid Systems is hiring developer</li>
      <li>- Northwell Consulting is looking for a decent designer</li>
    </ul>
    <div class="abs btn btn-small more-vac">More Vacancies</div>
  </div>

  <div class="abs social-box">
    <div class="sb-head">Bluvanta <span class="sb-like">Like</span></div>
    <div class="sb-count">8,046 people like <b>Bluvanta</b></div>
    <div class="faces" role="img" aria-label="Grid of follower profile photos"><span></span><span></span><span></span><span></span><span></span><span></span><span></span><span></span></div>
    <div class="sb-foot">Social plugin</div>
  </div>

  <div class="abs copy">Copyright © 2013 Bluvanta&nbsp; All rights reserved.&nbsp; /&nbsp;&nbsp; Site Map&nbsp; /&nbsp;&nbsp; Disclaimers</div>
</footer>
</body>
</html>
```